Open Harbor book needs a cover design

I need a front and back cover design that demonstrates a strong sense of possibility that trust can be repaired even if things look bleak. Repairing trust is difficult, but this book is full of wisdom, proven strategies, and doctoral research to help people strengthen relationships and improve trust. It can help any group: business, nonprofit, education, service. Showing diversity of groups and people is very important. For the cover title, there should be a play on words: "Open Harbor: Is it? Within Reach" should have the words "is it?" crossed out and the words "It IS! should be replaced there in a striking way. Perhaps in red ink. For publishing purposes, book will be titled Open Harbor: It IS Within Reach! Please see the attachment for an example. The book layout is approximately 260 pages.

A business self-help book, but the target is any person in a group that feels they have lost trust in each other. It can be just a normal person struggling in a volunteer group they are a part of, or a supervisor whose group is not working well together. It can be a leader who just wants their group to be stronger.

Business Management

• Allise - I believe is being used on the interior of the book for the title page and headings

• Show hope and possibility in the midst of difficulty. Must have a play on the words in the title "Open Harbor: Is it? Within Reach" with crossing out "is it?" with "It IS!" (see attached example) Must include the author's name: Marla Quentin, PhD Must include a smaller tagline: "Practical Steps to Move Teams Forward Again"
• Showing diverse people, or hands. Diverse kinds of groups - not just business. A colorful cover. Maybe show the complexity of trust when it is broken...broken pieces of trust that are then picked up and put together when people work together. Could show people (or images of hands) or other ways to show that it's a choice and it is possible to repair broken trust. I'd also like to convey a sense of a group - not just random people. That they have something at stake to work on repairing trust together and this book can help them.
• If images of people are used, just showing one gender or race is not okay. Nor just binary choices: like an image containing one man and one woman, or one white person and one person of color - otherwise it seems that the book on Open Harbor is about race or gender relations.

```html
<!DOCTYPE html>
<html lang="en">
<head>
<meta charset="utf-8">
<title>Open Harbor — Book Cover</title>
<link href="https://fonts.googleapis.com/css2?family=Oranienbaum&family=Cormorant+Garamond:wght@500&family=Montserrat:wght@700&display=swap" rel="stylesheet">
<style>
  :root {
    --ink-deep: #1b0f3d;
    --ink-mid: #2e1d6b;
    --violet: #5a3aa8;
    --lilac: #9c7fd6;
    --white: #ffffff;
    --red: #d8231f;
  }
  html, body { margin: 0; padding: 0; overflow: hidden; background: var(--ink-deep); }
  .cover {
    position: relative;
    width: 763px;
    height: 1200px;
    overflow: hidden;
    background:
      linear-gradient(160deg, transparent 55%, rgba(156,127,214,0.35) 62%, transparent 70%),
      linear-gradient(150deg, transparent 72%, rgba(180,150,235,0.45) 80%, rgba(90,58,168,0.6) 90%, transparent 100%),
      linear-gradient(170deg, transparent 20%, rgba(90,58,168,0.35) 28%, transparent 36%),
      linear-gradient(180deg, var(--ink-deep) 0%, var(--ink-mid) 45%, var(--violet) 100%);
  }
  .author {
    position: absolute;
    top: 40px;
    left: 0;
    width: 100%;
    text-align: center;
    font-family: "Cormorant Garamond", serif;
    font-weight: 500;
    font-size: 40px;
    letter-spacing: 0.22em;
    color: var(--white);
    margin: 0;
  }
  .title-art { position: absolute; top: 0; left: 0; }
  .title-art text { font-family: "Oranienbaum", serif; fill: var(--white); }
  .tagline {
    position: absolute;
    top: 622px;
    left: 0;
    width: 100%;
    text-align: center;
    font-family: "Cormorant Garamond", serif;
    font-weight: 500;
    font-size: 24px;
    line-height: 1.1;
    color: var(--white);
    text-transform: uppercase;
    margin: 0;
  }
  .group-illustration {
    position: absolute;
    top: 770px;
    left: 156px;
    width: 451px;
    height: 360px;
    border-radius: 10px;
    background: linear-gradient(135deg, #f1eef8 0%, #d9d0ee 55%, #bfb0e2 100%);
  }
  .publisher {
    position: absolute;
    top: 1140px;
    left: 0;
    width: 100%;
    display: flex;
    justify-content: center;
    align-items: center;
    gap: 10px;
    font-family: "Montserrat", sans-serif;
    font-weight: 700;
    font-size: 20px;
    letter-spacing: 0.06em;
    color: var(--white);
    text-transform: uppercase;
  }
  .publisher-mark { width: 22px; height: 22px; background: var(--white); }
</style>
</head>
<body>
  <main class="cover">
    <p class="author">MARLA QUENTIN, PHD</p>

    <svg class="title-art" width="763" height="640" viewBox="0 0 763 640" aria-label="Open Harbor: It IS Within Reach">
      <text x="194" y="287" font-size="185" textLength="380" lengthAdjust="spacingAndGlyphs">OPEN</text>
      <text x="194" y="440" font-size="185" textLength="380" lengthAdjust="spacingAndGlyphs">HARBOR</text>
      <g class="wordplay">
        <text x="194" y="572" font-size="38" textLength="84" lengthAdjust="spacingAndGlyphs">IT IS</text>
        <line x1="194" y1="578" x2="278" y2="578" stroke="var(--white)" stroke-width="3"/>
        <text x="194" y="612" font-size="38" textLength="84" lengthAdjust="spacingAndGlyphs">IS IT?</text>
        <path d="M188 606 C215 596 250 590 284 584 M190 594 C222 600 252 606 282 614" stroke="var(--red)" stroke-width="4" fill="none" stroke-linecap="round"/>
      </g>
      <text x="284" y="614" font-size="104" textLength="294" lengthAdjust="spacingAndGlyphs">WITHIN REACH</text>
    </svg>

    <p class="tagline">Practical Steps to<br>Move Teams Forward Again</p>

    <div class="group-illustration" role="img" aria-label="Interlocking puzzle pieces, each holding silhouettes of diverse people working together, with two people high-fiving in the centre"></div>

    <div class="publisher"><span class="publisher-mark"></span><span>Northgate Press</span></div>
  </main>
</body>
</html>
```